ORLA - Óptica Médica - web design and concept

Website concept - Create and develop our website design and structure. ORLA is an optical store chain, and we are looking to establish our web and digital concept. In attachment there are several pictures about our stores and our logo.

The website structure should be user friendly. Colors should be light and the design as simple and minimalist as possible. There are different variations of the logothat can be used, check the file.

The website will include optical collections and sun collections as an online store. Also, a medical menu should be considered in order for clients to schedule optometry appointments. There should also be a menu for client assistance where the clients can read about glass maintenance in our workshop.
Updates

Low design quality

Number of Pages Required

5+ page

Font styles to use
Serif
Sans Serif

Requirements
Must have
• Must be user-friendly and minimalist.
• Please USE PICTURES FROM THE BRANDS we sell: MERUN, BOSKA, PNW, KOLE, BAMPE
Nice to have
• Nice to inspire: ZEK glasses (see website https://ch.shopzek.com/en/)
• Nice to inspire: https://merun-eyewear.com/
• Nice to ispire: https://www.pnwglobe.com/en/
Should not have
• Hysteric colors and shapes

```html
<!DOCTYPE html>
<html lang="en">
<head>
<meta charset="utf-8">
<title>ORLA Óptica Médica – Product</title>
<link href="https://fonts.googleapis.com/css2?family=Lato:wght@300;400;700&family=Montserrat:wght@400;600&display=swap" rel="stylesheet">
<style>
:root{
  --gold:#ebb55c;
  --gold-dark:#d9a045;
  --ink:#222;
  --muted:#555;
  --band:#f5f5f6;
  --line:#e3e3e3;
  --footer:#000;
  --white:#fff;
}
*{margin:0;padding:0;box-sizing:border-box}
html,body{width:1200px;height:2195px;overflow:hidden;background:var(--white)}
body{font-family:"Lato",sans-serif;color:var(--ink);position:relative}
.abs{position:absolute}
a{color:inherit;text-decoration:none}

/* header */
.social{left:161px;top:15px;display:flex;gap:10px}
.social span{width:11px;height:11px;border-radius:50%;background:var(--ink);display:block}
.brand{left:0;width:1200px;top:14px;text-align:center}
.brand .mark{width:40px;height:40px;border:2px solid var(--ink);margin:0 auto 6px}
.brand .name{font-family:"Lato",sans-serif;font-size:22px;letter-spacing:5px;font-weight:400}
.brand .sub{font-size:7px;letter-spacing:2px;color:var(--muted)}
.cart{left:820px;top:15px;font-size:11px;display:flex;gap:6px;align-items:center}
.phone{left:937px;top:15px;font-size:11px;display:flex;gap:6px;align-items:center}
.nav{left:315px;top:105px;display:flex;gap:20px;font-size:11px;align-items:center}
.nav .active{color:var(--gold)}
.nav .cta{background:var(--gold);padding:4px 7px;color:var(--ink)}

.crumb{left:161px;top:166px;font-size:13px;font-weight:300}
.crumb em{font-style:normal;color:var(--gold)}

/* product */
.hero-img{left:158px;top:212px;width:410px;height:408px;background:radial-gradient(ellipse at 50% 50%,#5b6472 0%,#3a404a 22%,#eeeeee 40%,#eeeeee 100%)}
.info{left:622px;top:208px;width:420px}
.info h1{font-weight:300;font-size:26px}
.info .code{font-size:12px;margin-top:4px}
.info .price{font-weight:300;font-size:26px;margin-top:40px}
.info .stock{font-size:12px;color:var(--gold);margin-top:4px;font-weight:300}
.opts{display:flex;gap:24px;margin-top:30px}
.opt label{font-size:12px;display:block;margin-bottom:6px}
.select{width:100px;height:26px;border:1px solid var(--gold);display:flex;font-size:11px}
.select span{flex:1;display:flex;align-items:center;justify-content:center}
.select i{width:32px;background:var(--gold);display:flex;align-items:center;justify-content:center}
.qty{margin-top:28px}
.add{margin-top:50px;width:181px;height:53px;background:var(--gold);border:1px solid var(--gold-dark);font-size:13px;display:flex;align-items:center;justify-content:center}

.thumbs{left:116px;top:672px;width:490px;height:42px}
.thumb{position:absolute;top:8px;width:66px;height:26px;border-radius:12px;background:linear-gradient(#3b4350,#5c6675)}

/* tabs */
.tab{top:760px;height:43px;font-size:22px;font-weight:300;display:flex;align-items:center;justify-content:center}
.tab.one{left:161px;width:187px;background:var(--band)}
.tab.two{left:348px;width:220px;background:var(--gold);clip-path:polygon(0 0,80% 0,100% 100%,0 100%)}
.spec{left:0;top:803px;width:1200px;height:221px;background:var(--band);padding:47px 0 0 161px}
.spec p{font-size:18px;font-weight:300;height:43px;text-transform:uppercase}

/* titles */
.title{left:0;width:1200px;text-align:center;font-weight:300;font-size:25px}
.title::after{content:"";display:block;width:134px;height:4px;border-top:1px solid var(--gold);border-bottom:1px solid var(--gold);margin:12px auto 0}

/* related */
.chev{width:26px;height:44px}
.item{top:1156px;width:180px;text-align:center}
.item .pic{width:160px;height:70px;margin:0 auto;border-radius:30px}
.item p{margin-top:40px;font-size:17px;font-weight:300;color:var(--muted)}

/* features */
.feat{top:1371px;height:88px;border:2px solid var(--line);display:flex;align-items:center;gap:14px;padding-left:56px}
.feat h3{font-weight:300;font-size:18px;color:var(--muted)}
.feat small{font-size:11px;display:block}

/* partner band */
.partners{left:0;top:1496px;width:1200px;height:164px;background:var(--band)}
.partner{top:1562px;width:170px;text-align:center;font-family:"Lato",sans-serif;font-size:24px;font-weight:400;letter-spacing:1px}

/* newsletter */
.news{left:301px;top:1771px;width:595px;height:70px;border:2px solid #d6d9e3;display:flex}
.news span{flex:1;font-size:11px;padding-left:30px;display:flex;align-items:center}
.news button{width:91px;background:var(--gold);border:0;display:flex;align-items:center;justify-content:center}

/* footer */
.footer{left:0;top:1878px;width:1200px;height:317px;background:var(--footer);color:var(--white);font-family:"Montserrat",sans-serif}
.f-brand{left:161px;top:57px;width:160px}
.f-brand .mark{width:26px;height:26px;border:2px solid var(--gold)}
.f-brand .name{color:var(--gold);font-size:15px;letter-spacing:3px;margin-top:4px}
.f-brand p{font-size:10px;line-height:14px;margin-top:8px}
.f-brand .more{margin-top:8px;font-size:10px}
.f-social{display:flex;gap:10px;margin-top:10px}
.f-social span{width:10px;height:10px;border-radius:50%;background:var(--gold)}
.col{top:93px;font-size:10px}
.col h4{color:var(--gold);font-size:13px;font-weight:600;margin-bottom:17px}
.col li{list-style:none;height:16px;padding-left:14px;position:relative}
.col li::before{content:"";position:absolute;left:0;top:5px;width:3px;height:3px;border-radius:50%;background:var(--gold)}
.contact div{height:25px;display:flex;gap:8px;align-items:flex-start}
.rule{left:161px;top:225px;width:879px;height:1px;background:#555}
.copy{left:161px;top:240px;font-size:12px}
.legal{left:819px;top:235px;font-size:12px}
</style>
</head>
<body>

<header>
  <div class="abs social" aria-label="Social links"><span></span><span></span><span></span><span></span><span></span></div>
  <div class="abs brand">
    <div class="mark"></div>
    <div class="name">ORLA</div>
    <div class="sub">ÓPTICA MÉDICA</div>
  </div>
  <div class="abs cart">
    <svg width="10" height="11" viewBox="0 0 10 11"><rect x="1" y="4" width="8" height="7" fill="#222"/><path d="M3 4V2.5a2 2 0 0 1 4 0V4" stroke="#222" fill="none"/></svg>
    Your Cart &nbsp;( 0 )
  </div>
  <div class="abs phone">
    <svg width="10" height="10" viewBox="0 0 10 10"><path d="M2 0l2 2-1 2 3 3 2-1 2 2-2 2C4 10 0 6 0 2z" fill="#222"/></svg>
    +010-555-204-7
  </div>
  <nav class="abs nav">
    <a>Home</a><a class="active">Online store</a><a>Company history</a><a>Medical section</a><a>Store</a><a>Contact Us</a><a class="cta">Make an Appoinment</a>
  </nav>
</header>

<div class="abs crumb">Home / Online Store / <em>Product Name</em></div>

<main>
  <div class="abs hero-img" role="img" aria-label="Product photo: black aviator sunglasses with gold bridge and grey lenses"></div>

  <section class="abs info">
    <h1>Product Name</h1>
    <div class="code">Code : 10B0C</div>
    <div class="price">30.00 EUR</div>
    <div class="stock">In Stock</div>
    <div class="opts">
      <div class="opt"><label>Colour</label><div class="select"><span>Black</span><i><svg width="10" height="7"><path d="M0 0h10L5 7z" fill="#fff"/></svg></i></div></div>
      <div class="opt"><label>Size</label><div class="select"><span>Medium</span><i><svg width="10" height="7"><path d="M0 0h10L5 7z" fill="#fff"/></svg></i></div></div>
    </div>
    <div class="opt qty"><label>QTY</label><div class="select"><span>1</span><i><svg width="10" height="7"><path d="M0 0h10L5 7z" fill="#fff"/></svg></i></div></div>
    <div class="add">ADD TO CART</div>
  </section>

  <div class="abs thumbs">
    <svg class="abs" style="left:0;top:8px" width="14" height="26" viewBox="0 0 14 26"><path d="M13 1L1 13l12 12" stroke="#222" stroke-width="1.5" fill="none"/></svg>
    <div class="thumb" style="left:60px" role="img" aria-label="Sunglasses thumbnail"></div>
    <div class="thumb" style="left:162px" role="img" aria-label="Sunglasses thumbnail"></div>
    <div class="thumb" style="left:265px" role="img" aria-label="Sunglasses thumbnail"></div>
    <div class="thumb" style="left:369px" role="img" aria-label="Sunglasses thumbnail"></div>
    <svg class="abs" style="left:468px;top:8px" width="14" height="26" viewBox="0 0 14 26"><path d="M1 1l12 12L1 25" stroke="#ebb55c" stroke-width="1.5" fill="none"/></svg>
  </div>

  <div class="abs tab one">Discription</div>
  <div class="abs tab two">Loream</div>
  <section class="abs spec">
    <p>Size: Medium</p>
    <p>Measurements - 53x20x148</p>
    <p>Swiss Design</p>
    <p>Handmade In</p>
  </section>

  <h2 class="abs title" style="top:1068px">Related Product</h2>
  <svg class="abs chev" style="left:75px;top:1201px" viewBox="0 0 26 44"><path d="M24 2L3 22l21 20" stroke="#222" stroke-width="2" fill="none"/></svg>
  <div class="abs item" style="left:151px"><div class="pic" role="img" aria-label="Gold aviator sunglasses with green lenses" style="background:linear-gradient(#4f5a45,#6d7862)"></div><p>Product Name</p></div>
  <div class="abs item" style="left:391px"><div class="pic" role="img" aria-label="Tortoiseshell optical frames" style="background:linear-gradient(#8c4a1f,#b8773f)"></div><p>Product Name</p></div>
  <div class="abs item" style="left:626px"><div class="pic" role="img" aria-label="Black sunglasses with grey-blue lenses" style="background:linear-gradient(#2e343d,#6c7888)"></div><p>Product Name</p></div>
  <div class="abs item" style="left:867px"><div class="pic" role="img" aria-label="Black square sunglasses" style="background:linear-gradient(#111,#333)"></div><p>Product Name</p></div>
  <svg class="abs chev" style="left:1099px;top:1201px" viewBox="0 0 26 44"><path d="M2 2l21 20L2 42" stroke="#ebb55c" stroke-width="2" fill="none"/></svg>

  <section>
    <div class="abs feat" style="left:164px;width:285px">
      <svg width="26" height="30" viewBox="0 0 26 30"><circle cx="13" cy="12" r="10" stroke="#ebb55c" stroke-width="1.5" fill="none"/><path d="M9 24l4 5 4-5" stroke="#ebb55c" stroke-width="1.5" fill="none"/></svg>
      <div><h3>Free Shipping</h3><small>Lorem Ipsum is dummy text.</small></div>
    </div>
    <div class="abs feat" style="left:458px;width:285px">
      <svg width="30" height="30" viewBox="0 0 30 30"><circle cx="15" cy="13" r="9" stroke="#ebb55c" stroke-width="1.5" fill="none"/><path d="M5 14v-2a10 10 0 0 1 20 0v2M7 27c2-4 14-4 16 0" stroke="#ebb55c" stroke-width="1.5" fill="none"/></svg>
      <div><h3>Premium Support</h3><small>24/7 Customer service</small></div>
    </div>
    <div class="abs feat" style="left:752px;width:286px">
      <svg width="38" height="28" viewBox="0 0 38 28"><path d="M1 3h22v18H1zM23 9h8l6 7v5H23" stroke="#ebb55c" stroke-width="1.5" fill="none"/><circle cx="8" cy="23" r="3" fill="#fff" stroke="#ebb55c" stroke-width="1.5"/><circle cx="29" cy="23" r="3" fill="#fff" stroke="#ebb55c" stroke-width="1.5"/></svg>
      <div><h3>Payment Method</h3><small>Cash On Delivery</small></div>
    </div>
  </section>

  <section class="abs partners" aria-label="Brands we carry"></section>
  <svg class="abs chev" style="left:75px;top:1553px" viewBox="0 0 26 44"><path d="M24 2L3 22l21 20" stroke="#222" stroke-width="2" fill="none"/></svg>
  <div class="abs partner" style="left:145px">Corvane</div>
  <div class="abs partner" style="left:329px">Lumeo Paris</div>
  <div class="abs partner" style="left:515px">Nora Bell</div>
  <div class="abs partner" style="left:695px">ALTARIS</div>
  <div class="abs partner" style="left:881px">TESSO</div>
  <svg class="abs chev" style="left:1099px;top:1553px" viewBox="0 0 26 44"><path d="M2 2l21 20L2 42" stroke="#ebb55c" stroke-width="2" fill="none"/></svg>

  <h2 class="abs title" style="top:1696px">Subscribe For Our Newsletter</h2>
  <form class="abs news">
    <span>E-Mail Address</span>
    <button type="button" aria-label="Subscribe"><svg width="36" height="28" viewBox="0 0 36 28"><path d="M2 2l32 12L2 26l5-12zM7 14h27" stroke="#222" stroke-width="1.5" fill="none" stroke-linejoin="round"/></svg></button>
  </form>
</main>

<footer class="abs footer">
  <div class="abs f-brand">
    <div class="mark"></div>
    <div class="name">ORLA</div>
    <p>Lorem Ipsum is simply dummy text of the printing and typesetting industry.</p>
    <div class="more">READ MORE....</div>
    <div class="f-social"><span></span><span></span><span></span><span></span><span></span></div>
  </div>
  <div class="abs col" style="left:421px"><h4>QUICK LINK</h4><ul><li>Women</li><li>Men</li><li>Youth</li><li>Collections</li><li>Contact Us</li></ul></div>
  <div class="abs col" style="left:634px"><h4>ACCOUNT</h4><ul><li>My Account</li><li>My Wishlist</li><li>Checkout</li><li>Create Account</li><li>Register</li></ul></div>
  <div class="abs col contact" style="left:858px">
    <h4>QUICK CONTACT</h4>
    <div><svg width="9" height="9" viewBox="0 0 10 10"><path d="M2 0l2 2-1 2 3 3 2-1 2 2-2 2C4 10 0 6 0 2z" fill="#ebb55c"/></svg>+010-555-204-7</div>
    <div><svg width="10" height="8" viewBox="0 0 10 8"><rect width="10" height="8" fill="#ebb55c"/><path d="M0 0l5 4 5-4" stroke="#000" fill="none"/></svg>hello@orlaopticamedica.com</div>
    <div><svg width="8" height="11" viewBox="0 0 8 11"><path d="M4 11L1 6a3.5 3.5 0 1 1 6 0z" fill="#ebb55c"/></svg>14 Alder Row,<br>Brookfield Vale, NB 20415</div>
  </div>
  <div class="abs rule"></div>
  <div class="abs copy">CopyRight ©2018 ORLA Optica Medica. All Right Reserve</div>
  <div class="abs legal">Privacy Policy - Terms &amp; Conditions</div>
</footer>

</body>
</html>
```